Audio-Visual & Video Communications Business Requires a Cutting-edge Business Card Design

LinkVerra is a new Audio-Visual & Video Communications company in Cape Town, South Africa that is looking for a cutting-edge business card design. We sell these products to the Corporate, Education & Hospitality markets and will also host an Online Shop for companies and individuals to purchase our products online.

We are already using the following two colours in our logo and draft website. Please incorporate these colours into the design. Please note that our website is still in the design stage if you need to visit it. Green #a0ce4e & Dark Grey #333333.

Hi,

Please note that I have uploaded our logo in an .eps format.

Target Market(s)

Corporate Companies, Education Institutions & Hospitality Markets

Industry/Entity Type

Business

Requirements
Nice to have
• It would be great if you could incorporate the services that we offer.

1. Consultation & Design
2. Project Management
3. Supply & Installation
4. Onsite Support Personal
5. Online Shop

```html
<!DOCTYPE html>
<html lang="en">
<head>
<meta charset="utf-8">
<title>LinkVerra Business Card</title>
<link rel="stylesheet" href="https://fonts.googleapis.com/css2?family=Open+Sans:wght@400;600;700&display=swap">
<style>
  :root {
    --brand-green: #a0ce4e;
    --brand-grey: #333333;
    --card-white: #ffffff;
    --backdrop: #3c3c3c;
    --divider-shadow: rgba(0, 0, 0, 0.18);
    --divider-light: rgba(255, 255, 255, 0.35);
  }
  * { box-sizing: border-box; margin: 0; padding: 0; }
  html, body {
    width: 1200px;
    height: 960px;
    overflow: hidden;
  }
  body {
    background: var(--backdrop);
    font-family: "Open Sans", Arial, sans-serif;
    position: relative;
  }
  .card {
    position: absolute;
    width: 620px;
    height: 344px;
    border-radius: 18px;
    box-shadow: 0 6px 18px rgba(0, 0, 0, 0.35);
  }
  /* Front */
  .card-front {
    left: 120px;
    top: 120px;
    background: var(--card-white);
    display: flex;
    align-items: center;
    justify-content: center;
  }
  .wordmark {
    display: flex;
    align-items: center;
    gap: 16px;
  }
  .wordmark-dot {
    width: 34px;
    height: 34px;
    border-radius: 50%;
    background: var(--brand-grey);
  }
  .wordmark-name {
    font-weight: 700;
    font-size: 46px;
    letter-spacing: -0.5px;
    color: var(--brand-green);
  }
  /* Back */
  .card-back {
    left: 460px;
    top: 496px;
    background: var(--brand-green);
    overflow: hidden;
  }
  .back-mark-panel {
    position: absolute;
    left: 0;
    top: 0;
    width: 186px;
    height: 100%;
    display: flex;
    align-items: center;
    justify-content: center;
  }
  .back-mark-dot {
    width: 56px;
    height: 56px;
    border-radius: 50%;
    background: var(--brand-grey);
  }
  .back-divider {
    position: absolute;
    left: 186px;
    top: 72px;
    width: 3px;
    height: 190px;
    background: linear-gradient(to right, var(--divider-shadow), var(--divider-light));
    border-radius: 2px;
  }
  .contact {
    position: absolute;
    right: 38px;
    top: 104px;
    text-align: right;
    color: var(--brand-grey);
  }
  .contact-name {
    font-weight: 600;
    font-size: 27px;
    line-height: 1.05;
  }
  .contact-role {
    font-weight: 400;
    font-size: 21px;
    line-height: 1.15;
    margin-bottom: 12px;
  }
  .contact-line {
    font-weight: 400;
    font-size: 17px;
    line-height: 1.3;
  }
</style>
</head>
<body>
  <section class="card card-front" aria-label="Business card front">
    <div class="wordmark">
      <span class="wordmark-dot"></span>
      <span class="wordmark-name">LinkVerra</span>
    </div>
  </section>

  <section class="card card-back" aria-label="Business card back">
    <div class="back-mark-panel"><span class="back-mark-dot"></span></div>
    <div class="back-divider"></div>
    <div class="contact">
      <p class="contact-name">Daniel Mercer</p>
      <p class="contact-role">Director</p>
      <p class="contact-line">mobile: 21 4870.2615</p>
      <p class="contact-line">daniel@linkverra.com</p>
    </div>
  </section>
</body>
</html>
```